Plakat-Design für kleine deutsche Immobilien- und Reiseveranstalter-Firma
Zielgruppe
Kleine deutsche Immobilien- und Reiseveranstalter-Firma, spezialisiert auf Italien. In Italien sind es Immobilienbesitzer, die aus versch. Gründen hoffen an Ausländer zu verkaufen/vermieten ( Alter ca. ab 35-40)
Aufgabenstellung
Um neue Immo-Besitzer anzusprechen, lassen wir in verschiedenen Gemeinden in der Nordtoskana Plakate gegen Gebühr kleben ( 70 x 100, meistens 1 bis 2 Wochen)
Text auf Italienisch
Was an Text rein muss( falls Sie es anders mitteilen wollen, bin ich gerne bereit es zu diskutieren)
VUOI VENDERE CASA A STRANIERI O AFFITTARLA A TURISTI ? (Übersetzung ca.:= wollen Sie Ihre Immobilie an Ausländer verkaufen oder an Touristen vermieten?)
Verdona
Germania – info@verdona-beispiel.de + 49 7412 3810457
Italia – 0571 – 394062, Cell.: 371 – 2094716, 335- 47 92608,
www.verdonacase-beispiel.com
www.verdonaaffitti-beispiel.com
Der Poster, den man meistens im Vorbeifahren sieht, soll springt sofort ins Auge , fast aufdringlich. Man kann mit Farben oder Bildern (oder beiden) arbeiten. Stechende Farben, sonst minimalistisch einfach. (??)
Erfahrung zeigt, daß die beiden Mobile Nummern (Cell.:) mehr sichtbar sein könnten. Ich kann zwei letzte zeigen, aber ungern, weil sie mir nicht gefallen und Neues – besseres suche.
PS: habe mal so was wie Guerilla -Marketing versucht – wurde nicht verstanden.
Bilder kann ich nach Wunsch liefern.

```html
<!DOCTYPE html>
<html lang="it">
<head>
<meta charset="utf-8">
<title>Verdona – Vuoi vendere casa a stranieri o affittarla a turisti?</title>
<link rel="stylesheet" href="https://fonts.googleapis.com/css2?family=Montserrat:wght@400;500;600;700;800;900&display=swap">
<style>
  :root {
    --page-bg: #56708f;
    --panel-mint: #effdf1;
    --ink: #050a09;
    --ink-teal: #07302b;
    --deep-green: #03221f;
    --accent-green: #2fcf5c;
    --white: #ffffff;
  }
  * { box-sizing: border-box; margin: 0; padding: 0; }
  html, body { width: 1200px; height: 1177px; overflow: hidden; }
  body {
    background: var(--page-bg);
    font-family: "Montserrat", Arial, sans-serif;
    color: var(--ink);
    position: relative;
  }
  .poster {
    position: absolute;
    left: 199px; top: 20px;
    width: 803px; height: 1137px;
    background: var(--white);
  }
  .photo { position: absolute; }
  .photo--beach {
    left: 0; top: 0; width: 391px; height: 290px;
    background: linear-gradient(180deg, #5fc3ea 0%, #8fd6ee 32%, #2fb3b6 34%, #3cbcc0 40%, #e9d6a4 48%, #e4cc92 75%, #b79a6a 100%);
  }
  .photo--terrace {
    left: 411px; top: 0; width: 392px; height: 290px;
    background: linear-gradient(160deg, #b8c9d6 0%, #9f9685 30%, #d9d5cc 55%, #8f918a 80%, #a09a8e 100%);
  }
  .photo--bedroom {
    left: 411px; top: 306px; width: 392px; height: 291px;
    background: linear-gradient(160deg, #e8e8e6 0%, #cfd3cc 30%, #d9d0c5 55%, #f1f1f3 80%, #e5e6ea 100%);
  }
  .photo--living {
    left: 411px; top: 612px; width: 392px; height: 291px;
    background: linear-gradient(165deg, #f2f2f1 0%, #dcdcdc 35%, #c89a63 55%, #e9d6be 80%, #e7d3b8 100%);
  }

  .intro-panel {
    position: absolute;
    left: 0; top: 306px; width: 391px; height: 831px;
    background: var(--panel-mint);
  }
  .brand {
    position: absolute;
    left: 50px; top: 40px;
    display: flex; align-items: center; gap: 10px;
  }
  .brand__dot {
    width: 22px; height: 22px; border-radius: 50%;
    background: var(--accent-green);
  }
  .brand__name {
    font-weight: 800; font-size: 60px; letter-spacing: -0.5px;
    color: var(--ink); line-height: 1;
  }
  .headline { position: absolute; left: 49px; top: 194px; }
  .headline__big {
    display: block;
    font-weight: 900; font-size: 57px; line-height: 64px;
    letter-spacing: -0.5px;
  }
  .headline__big--first { color: var(--ink-teal); }
  .headline__line {
    display: block;
    font-weight: 800; font-size: 27px; line-height: 45px;
    letter-spacing: 0.2px;
  }
  .headline__line:first-of-type { margin-top: 2px; }
  .translation {
    position: absolute; left: 51px; top: 486px; width: 330px;
    font-weight: 500; font-size: 19px; line-height: 29px;
  }

  .country-tab {
    position: absolute; left: 0; width: 168px; height: 76px;
    background: var(--deep-green);
    color: var(--accent-green);
    font-weight: 700; font-size: 17px;
    display: flex; align-items: center; padding-left: 48px;
  }
  .country-tab--de { top: 610px; letter-spacing: 0.5px; }
  .country-tab--it { top: 705px; letter-spacing: 3px; }

  .contact { position: absolute; left: 180px; display: flex; align-items: center; gap: 12px; font-weight: 500; }
  .contact svg { flex: none; }
  .contact__text { font-size: 16.5px; line-height: 1; white-space: nowrap; }
  .contact__text--mail { font-size: 13px; }
  .contact--mail { top: 619px; }
  .contact--de-phone { top: 658px; }
  .contact--it-phone { top: 708px; }
  .contact--mobiles { top: 734px; align-items: flex-start; }
  .contact--mobiles .contact__text { line-height: 25px; }

  .online-box {
    position: absolute; left: 411px; top: 919px; width: 392px; height: 218px;
    background: var(--deep-green); color: var(--white);
  }
  .online-box__web { position: absolute; left: 38px; top: 34px; display: flex; align-items: center; gap: 12px; }
  .online-box__urls { font-weight: 500; font-size: 15.5px; line-height: 29px; }
  .online-box__urls strong { color: var(--accent-green); font-weight: 700; }
  .online-box__social { position: absolute; left: 38px; top: 115px; display: flex; align-items: center; gap: 14px; }
  .online-box__square { width: 29px; height: 29px; border-radius: 3px; background: var(--accent-green); }
  .online-box__handle { font-weight: 500; font-size: 19px; }
</style>
</head>
<body>
  <main class="poster">
    <div class="photo photo--beach" role="img" aria-label="Sentiero in legno tra le dune verso il mare turchese"></div>
    <div class="photo photo--terrace" role="img" aria-label="Terrazza con pergolato bianco accanto a un trullo in pietra"></div>
    <div class="photo photo--bedroom" role="img" aria-label="Camera da letto luminosa con cassettiera e finestra aperta"></div>
    <div class="photo photo--living" role="img" aria-label="Soggiorno con tavolo in legno, sedie bianche e televisore"></div>

    <section class="intro-panel">
      <div class="brand">
        <span class="brand__dot"></span>
        <span class="brand__name">Verdona</span>
      </div>
      <h1 class="headline">
        <span class="headline__big headline__big--first">VUOI</span>
        <span class="headline__big">VENDERE</span>
        <span class="headline__line">CASA A STRANIERI</span>
        <span class="headline__line">O AFFITTARLA</span>
        <span class="headline__line">A TURISTI ?</span>
      </h1>
      <p class="translation" lang="de">wollen Sie Ihre Immobilie an Ausländer verkaufen oder an Touristen vermieten?</p>

      <div class="country-tab country-tab--de">GERMANIA</div>
      <div class="country-tab country-tab--it">ITALIA</div>

      <div class="contact contact--mail">
        <svg width="25" height="18" viewBox="0 0 25 18"><rect x="1" y="1" width="23" height="16" fill="none" stroke="#2fcf5c" stroke-width="2"/><path d="M1 1 L12.5 10 L24 1 M1 17 L9 8.5 M24 17 L16 8.5" fill="none" stroke="#2fcf5c" stroke-width="2"/></svg>
        <span class="contact__text contact__text--mail">info@verdona-beispiel.de</span>
      </div>
      <div class="contact contact--de-phone">
        <svg width="24" height="24" viewBox="0 0 24 24"><path d="M5 2 L9 2 L10.5 7 L8 9 C9.5 12 12 14.5 15 16 L17 13.5 L22 15 L22 19 C22 20.5 20.5 22 19 22 C10 21.5 2.5 14 2 5 C2 3.5 3.5 2 5 2 Z" fill="#2fcf5c"/><path d="M14 2 A8 8 0 0 1 22 10 M14 6 A4 4 0 0 1 18 10" fill="none" stroke="#2fcf5c" stroke-width="1.8"/></svg>
        <span class="contact__text">+ 49 7412 3810457</span>
      </div>
      <div class="contact contact--it-phone">
        <svg width="24" height="24" viewBox="0 0 24 24"><path d="M5 2 L9 2 L10.5 7 L8 9 C9.5 12 12 14.5 15 16 L17 13.5 L22 15 L22 19 C22 20.5 20.5 22 19 22 C10 21.5 2.5 14 2 5 C2 3.5 3.5 2 5 2 Z" fill="#2fcf5c"/><path d="M14 2 A8 8 0 0 1 22 10 M14 6 A4 4 0 0 1 18 10" fill="none" stroke="#2fcf5c" stroke-width="1.8"/></svg>
        <span class="contact__text">0571 – 394062</span>
      </div>
      <div class="contact contact--mobiles">
        <svg width="22" height="36" viewBox="0 0 22 36"><rect x="2" y="1.5" width="18" height="33" rx="3" fill="none" stroke="#2fcf5c" stroke-width="2.4"/><line x1="2" y1="6.5" x2="20" y2="6.5" stroke="#2fcf5c" stroke-width="2"/><line x1="2" y1="28" x2="20" y2="28" stroke="#2fcf5c" stroke-width="2"/><circle cx="11" cy="31.3" r="1.4" fill="#2fcf5c"/></svg>
        <span class="contact__text">371 – 2094716<br>335- 47 92608</span>
      </div>
    </section>

    <section class="online-box">
      <div class="online-box__web">
        <svg width="30" height="30" viewBox="0 0 30 30"><circle cx="15" cy="15" r="15" fill="#2fcf5c"/><g fill="none" stroke="#03221f" stroke-width="1.6"><circle cx="15" cy="15" r="9"/><ellipse cx="15" cy="15" rx="4" ry="9"/><line x1="6" y1="15" x2="24" y2="15"/><line x1="7.5" y1="10.5" x2="22.5" y2="10.5"/><line x1="7.5" y1="19.5" x2="22.5" y2="19.5"/></g></svg>
        <div class="online-box__urls">
          <div>www.<strong>verdonacase-beispiel</strong>.com</div>
          <div>www.<strong>verdonaaffitti-beispiel</strong>.com</div>
        </div>
      </div>
      <div class="online-box__social">
        <span class="online-box__square"></span>
        <span class="online-box__handle">verdonacase</span>
      </div>
    </section>
  </main>
</body>
</html>
```